I will ask the design of the business card

We are looking for business card design of the new company "R DOVE PAYGRID WORKS LLC." Based in Azerbaijan.
In case
We are working on Azerbaijan to set up the first exchange of crypto currencies.

The key currency used in exchanges is called "PLUME".
In case
We are doing project to make crypto currency infrastructure.

We provide state-of-the-art technology to the world.

```html
<!DOCTYPE html>
<html lang="en">
<head>
<meta charset="utf-8">
<title>R Dove Paygrid Works LLC. – Business Card</title>
<link rel="stylesheet" href="https://fonts.googleapis.com/css2?family=Open+Sans:wght@400;600&display=swap">
<style>
  :root {
    --backdrop: #2c2c2c;
    --card-light: #efefef;
    --brand-blue: #0480c1;
    --ink: #333333;
    --rule: #a9a9a9;
    --white: #ffffff;
  }
  * { margin: 0; padding: 0; box-sizing: border-box; }
  html, body {
    width: 1200px; height: 1200px; overflow: hidden;
    background: var(--backdrop);
    font-family: "Open Sans", Arial, sans-serif;
  }
  .canvas { position: relative; width: 1200px; height: 1200px; }
  .card {
    position: absolute; top: 310px; height: 594px;
    box-shadow: 3px 4px 8px rgba(0,0,0,0.45);
  }
  .card--front { left: 234px; width: 364px; background: var(--card-light); }
  .card--back  { left: 627px; width: 369px; background: var(--brand-blue); }

  .brand-name {
    position: absolute; left: 0; right: 0;
    text-align: center; font-weight: 600; font-size: 26px;
    line-height: 34px; letter-spacing: 0.5px;
  }
  .card--front .brand-name { top: 462px - 310px; top: 150px; color: var(--brand-blue); }
  .card--back  .brand-name { top: 258px; color: var(--white); }

  .contact-block {
    position: absolute; left: 0; right: 0; top: 335px;
    text-align: center; color: var(--ink);
  }
  .person-name { font-size: 21px; font-weight: 600; color: var(--brand-blue); line-height: 26px; }
  .person-role { font-size: 17px; line-height: 22px; }
  .divider { width: 208px; height: 1px; background: var(--rule); margin: 8px auto 12px; }
  .contact-line { font-size: 16.5px; line-height: 21.5px; }
  .contact-line .label { color: var(--brand-blue); font-weight: 600; }
  .website { font-size: 16.5px; line-height: 21.5px; font-weight: 600; color: var(--brand-blue); }
  .address { font-size: 16.5px; line-height: 21.5px; }
</style>
</head>
<body>
<main class="canvas">
  <section class="card card--front">
    <p class="brand-name">R DOVE<br>PAYGRID WORKS LLC.</p>
    <div class="contact-block">
      <p class="person-name">DANIEL HARPER</p>
      <p class="person-role">Managing Director</p>
      <div class="divider"></div>
      <p class="contact-line"><span class="label">P:</span> 055-210 384 617</p>
      <p class="contact-line"><span class="label">M:</span> 055-210 384 618</p>
      <p class="contact-line"><span class="label">E:</span> info@dovepaygrid.az</p>
      <p class="website">www.dovepaygrid.az</p>
      <div class="divider"></div>
      <p class="address">27 Nizami Street, Suite 4<br>Baku, Azerbaijan, AZ1000.</p>
    </div>
  </section>
  <section class="card card--back">
    <p class="brand-name">R DOVE<br>PAYGRID WORKS LLC.</p>
  </section>
</main>
</body>
</html>
```